Nivel Crest - Powerpoint Templates

We are a consultancy to help builders to optimize their planning in order to save building costs. For that reason we need templates for teasers and presentations where we offer our services, show our team and their capacities and present workflows, organization charts, price lists etc.

```html
<!DOCTYPE html>
<html lang="en">
<head>
<meta charset="utf-8">
<title>Nivel Crest – Presentation Template</title>
<link href="https://fonts.googleapis.com/css2?family=Montserrat:wght@500;700;800&family=Open+Sans:wght@400;700&display=swap" rel="stylesheet">
<style>
:root{
  --board:#4b4b4b;
  --gold:#b47b0a;
  --gold-light:#d39a1c;
  --gold-grad:linear-gradient(90deg,#a86f06,#d49b1e);
  --ink:#1d1d1d;
  --dark:#1f1f1f;
  --body:#3a3a3a;
  --panel:#f2f2f2;
  --white:#ffffff;
  --grey-ring:#c9c9c9;
}
*{box-sizing:border-box;margin:0;padding:0}
html,body{width:1200px;height:713px;overflow:hidden;background:var(--board)}
.stage{position:absolute;left:0;top:0;width:2500px;height:1484px;transform:scale(.48);transform-origin:0 0}
.slide{position:absolute;width:762px;height:428px;overflow:hidden;background:var(--white);font-family:"Open Sans",sans-serif;color:var(--body)}
.abs{position:absolute}
.photo{position:absolute}
.brand{position:absolute;display:flex;align-items:center;gap:6px}
.brand-mark{width:14px;height:14px;background:var(--gold)}
.brand-name{font-family:"Montserrat",sans-serif;font-weight:700;color:var(--gold);font-size:15px;letter-spacing:1.5px;white-space:nowrap}
.heading{position:absolute;font-family:"Montserrat",sans-serif;font-weight:800;color:var(--ink);font-size:22px;line-height:29px;text-transform:uppercase}
.heading .accent{color:var(--gold)}
.copy{position:absolute;font-size:6.4px;line-height:12px}
.copy p+p{margin-top:11px}
.item{position:absolute;width:190px;padding-left:34px}
.item h4{font-size:7.6px;font-weight:700;color:var(--ink);margin-bottom:4px}
.item p{font-size:6px;line-height:11px}
.tick{position:absolute;left:0;top:0;width:22px;height:22px;border-radius:50%;background:var(--gold)}
.tick::after{content:"";position:absolute;left:7px;top:6px;width:7px;height:4px;border-left:2px solid #fff;border-bottom:2px solid #fff;transform:rotate(-45deg)}
.band{position:absolute;background:var(--gold-grad)}
.slant-left{clip-path:polygon(0 0,100% 0,calc(100% - 40px) 100%,0 100%)}
.slant-right{clip-path:polygon(40px 0,100% 0,100% 100%,0 100%)}
.top-slant{clip-path:polygon(0 0,100% 0,100% 100%,35px 100%)}
.on-dark{color:#e3e3e3}
</style>
</head>
<body>
<div class="stage">

  <!-- Cover -->
  <section class="slide cover" style="left:62px;top:55px;background:#1a1a1a">
    <div class="photo" role="img" aria-label="Darkened photo of a modern house at dusk" style="inset:0;background:linear-gradient(135deg,#2e2e2e 0%,#1d1d1d 55%,#141414 100%)"></div>
    <div class="brand" style="left:322px;top:200px;gap:12px">
      <span class="brand-mark" style="width:34px;height:34px"></span>
      <span class="brand-name" style="font-size:40px;letter-spacing:4px">NIVEL CREST</span>
    </div>
    <div class="abs" style="left:316px;top:310px;font-family:Montserrat,sans-serif;font-weight:700;font-size:28px;letter-spacing:4px;color:var(--gold-light)">PROJECT TITLE HERE</div>
    <div class="abs" style="left:316px;top:348px;font-family:Montserrat,sans-serif;font-weight:700;font-size:17px;letter-spacing:3px;color:#fff">PRESENTER NAME HERE</div>
  </section>

  <!-- About -->
  <section class="slide about" style="left:852px;top:61px">
    <div class="band" style="left:0;top:0;width:139px;height:428px"></div>
    <div class="band top-slant" style="left:513px;top:0;width:249px;height:25px"></div>
    <div class="photo" role="img" aria-label="Black and white photo of a business team pulling a rope together" style="left:33px;top:33px;width:305px;height:365px;background:linear-gradient(160deg,#8a8a8a,#4a4a4a 50%,#9c9c9c)"></div>
    <div class="heading" style="left:376px;top:88px;font-size:18px">About our <span class="accent">Nivel Crest</span></div>
    <div class="copy" style="left:376px;top:118px;width:355px">
      <p>We help builders plan every phase with care, so budgets hold, schedules stay firm and costly surprises on site are caught long before the first stone is laid.</p>
      <p>Our consultants review drawings, tenders and contracts, compare offers and point out savings that make a real difference to your final building cost.</p>
      <p>We help builders plan every phase with care, so budgets hold, schedules stay firm and costly surprises on site are caught long before the first stone is laid.</p>
      <p>Talk to us early and save more.</p>
    </div>
    <div class="brand" style="left:588px;top:396px">
      <span class="brand-mark" style="width:10px;height:10px"></span>
      <span class="brand-name" style="font-size:12px">NIVEL CREST</span>
    </div>
  </section>

  <!-- Mission -->
  <section class="slide mission" style="left:1655px;top:63px">
    <div class="photo" role="img" aria-label="Dark toned photo of a smiling business team" style="left:0;top:0;width:762px;height:214px;background:linear-gradient(100deg,#262626 0%,#2f2f2f 55%,#3a3a3a 100%)"></div>
    <div class="brand" style="left:566px;top:20px">
      <span class="brand-mark" style="width:11px;height:11px"></span>
      <span class="brand-name" style="font-size:13px">NIVEL CREST</span>
    </div>
    <div class="heading" style="left:56px;top:42px;color:#fff">Our mission, vision <span class="accent">and</span><br><span class="accent">project goals</span></div>
    <div class="copy on-dark" style="left:56px;top:108px;width:445px">
      <p>We help builders plan every phase with care, so budgets hold, schedules stay firm and costly surprises on site are caught long before the first stone is laid.</p>
      <p>Our consultants review drawings, tenders and contracts, compare offers and point out savings that make a real difference to your final building cost.</p>
    </div>
    <div class="item" style="left:66px;top:260px"><span class="tick"></span><h4>Your Title Text One</h4><p>Clear cost checks at every stage keep your project on budget and on time.</p></div>
    <div class="item" style="left:298px;top:260px"><span class="tick"></span><h4>Your Title Text Two</h4><p>Clear cost checks at every stage keep your project on budget and on time.</p></div>
    <div class="item" style="left:530px;top:260px"><span class="tick"></span><h4>Your Title Text Three</h4><p>Clear cost checks at every stage keep your project on budget and on time.</p></div>
    <div class="item" style="left:66px;top:332px"><span class="tick"></span><h4>Your Title Text Four</h4><p>Clear cost checks at every stage keep your project on budget and on time.</p></div>
    <div class="item" style="left:298px;top:332px"><span class="tick"></span><h4>Your Title Text Five</h4><p>Clear cost checks at every stage keep your project on budget and on time.</p></div>
    <div class="item" style="left:530px;top:332px"><span class="tick"></span><h4>Your Title Text Six</h4><p>Clear cost checks at every stage keep your project on budget and on time.</p></div>
  </section>

  <!-- Overview chart -->
  <section class="slide overview" style="left:60px;top:527px">
    <div class="brand" style="left:556px;top:26px">
      <span class="brand-mark" style="width:12px;height:12px"></span>
      <span class="brand-name" style="font-size:14px">NIVEL CREST</span>
    </div>
    <div class="heading" style="left:56px;top:74px">Annual <span class="accent">project overview</span></div>
    <div class="copy" style="left:56px;top:112px;width:450px">
      <p>We help builders plan every phase with care, so budgets hold, schedules stay firm and costly surprises on site are caught long before the first stone is laid.</p>
      <p>Our consultants review drawings, tenders and contracts, compare offers and point out savings that make a real difference to your final building cost.</p>
    </div>
    <svg class="abs chart" style="left:0;top:0" width="762" height="428" viewBox="0 0 762 428" font-family="Open Sans, sans-serif" font-size="6.5" fill="#444">
      <g stroke="#e6e6e6" stroke-width="1">
        <line x1="72" y1="210" x2="705" y2="210"/><line x1="72" y1="247" x2="705" y2="247"/>
        <line x1="72" y1="284" x2="705" y2="284"/><line x1="72" y1="321" x2="705" y2="321"/>
        <line x1="72" y1="358" x2="705" y2="358" stroke="#cfcfcf"/>
      </g>
      <g text-anchor="end">
        <text x="67" y="212">70k</text><text x="67" y="249">60k</text><text x="67" y="286">40k</text><text x="67" y="323">20k</text><text x="67" y="360">0k</text>
      </g>
      <g fill="#e0e0e0">
        <rect x="86" y="341" width="24" height="17"/><rect x="134" y="326" width="24" height="32"/><rect x="183" y="296" width="24" height="62"/>
        <rect x="231" y="220" width="24" height="138"/><rect x="279" y="275" width="24" height="83"/><rect x="328" y="301" width="24" height="57"/>
        <rect x="376" y="332" width="24" height="26"/><rect x="424" y="275" width="24" height="83"/><rect x="473" y="305" width="24" height="53"/>
        <rect x="521" y="328" width="24" height="30"/><rect x="569" y="287" width="24" height="71"/><rect x="618" y="238" width="24" height="120"/>
        <rect x="666" y="299" width="24" height="59"/>
      </g>
      <g fill="#b47b0a">
        <rect x="86" y="346" width="24" height="12"/><rect x="134" y="335" width="24" height="23"/><rect x="183" y="309" width="24" height="49"/>
        <rect x="231" y="242" width="24" height="116"/><rect x="279" y="296" width="24" height="62"/><rect x="328" y="306" width="24" height="52"/>
        <rect x="376" y="335" width="24" height="23"/><rect x="424" y="296" width="24" height="62"/><rect x="473" y="314" width="24" height="44"/>
        <rect x="521" y="340" width="24" height="18"/><rect x="569" y="309" width="24" height="49"/><rect x="618" y="257" width="24" height="101"/>
        <rect x="666" y="311" width="24" height="47"/>
      </g>
      <g text-anchor="middle">
        <text x="98" y="373">2014</text><text x="146" y="373">2015</text><text x="195" y="373">2016</text><text x="243" y="373">2017</text>
        <text x="291" y="373">2018</text><text x="340" y="373">2020</text><text x="388" y="373">2014</text><text x="436" y="373">2015</text>
        <text x="485" y="373">2016</text><text x="533" y="373">2017</text><text x="581" y="373">2018</text><text x="630" y="373">2020</text>
        <text x="678" y="373">2020</text>
      </g>
    </svg>
  </section>

  <!-- Numbered steps -->
  <section class="slide steps" style="left:854px;top:530px">
    <div class="band" style="left:623px;top:0;width:139px;height:428px"></div>
    <div class="band slant-left" style="left:0;top:403px;width:250px;height:25px"></div>
    <div class="photo" role="img" aria-label="Photo of two construction engineers in hard hats pointing at a building" style="left:388px;top:31px;width:342px;height:365px;background:linear-gradient(150deg,#b8c4cf,#8c9cab 45%,#c9a98a 100%)"></div>
    <div class="brand" style="left:18px;top:18px">
      <span class="brand-mark" style="width:12px;height:12px"></span>
      <span class="brand-name" style="font-size:14px">NIVEL CREST</span>
    </div>
    <div class="heading" style="left:56px;top:70px">Lorem ipsum <span class="accent">dolor</span><br><span class="accent">sit amet</span></div>
    <div class="abs" style="left:72px;top:138px;width:296px;height:69px;background:var(--panel);clip-path:polygon(0 0,100% 0,88% 100%,0 100%)"></div>
    <div class="abs" style="left:72px;top:216px;width:296px;height:69px;background:var(--panel);clip-path:polygon(0 0,100% 0,88% 100%,0 100%)"></div>
    <div class="abs" style="left:72px;top:294px;width:296px;height:69px;background:var(--panel);clip-path:polygon(0 0,100% 0,88% 100%,0 100%)"></div>
    <div class="step" style="position:absolute;left:57px;top:156px;width:34px;height:34px;border-radius:50%;background:var(--gold);color:#fff;font:700 8px Montserrat,sans-serif;display:flex;align-items:center;justify-content:center">01</div>
    <div class="step" style="position:absolute;left:57px;top:234px;width:34px;height:34px;border-radius:50%;background:var(--gold);color:#fff;font:700 8px Montserrat,sans-serif;display:flex;align-items:center;justify-content:center">01</div>
    <div class="step" style="position:absolute;left:57px;top:311px;width:34px;height:34px;border-radius:50%;background:var(--gold);color:#fff;font:700 8px Montserrat,sans-serif;display:flex;align-items:center;justify-content:center">01</div>
    <div class="item" style="left:67px;top:149px;width:270px"><h4>Your Title Text One</h4><p>Short summary of this service step, what it covers and how it saves money for builders.</p></div>
    <div class="item" style="left:67px;top:227px;width:270px"><h4>Your Title Text Two</h4><p>Short summary of this service step, what it covers and how it saves money for builders.</p></div>
    <div class="item" style="left:67px;top:305px;width:270px"><h4>Your Title Text Three</h4><p>Short summary of this service step, what it covers and how it saves money for builders.</p></div>
  </section>

  <!-- Progress -->
  <section class="slide progress" style="left:1653px;top:533px">
    <div class="band slant-right" style="left:510px;top:402px;width:252px;height:26px"></div>
    <div class="brand" style="left:558px;top:24px">
      <span class="brand-mark" style="width:12px;height:12px"></span>
      <span class="brand-name" style="font-size:14px">NIVEL CREST</span>
    </div>
    <div class="heading" style="left:56px;top:62px">Lorem ipsum <span class="accent">dolor</span><br><span class="accent">sit amet</span></div>
    <div class="copy" style="left:56px;top:128px;width:320px">
      <p>We help builders plan every phase with care, so budgets hold, schedules stay firm and costly surprises on site are caught long before the first stone is laid.</p>
      <p>Our consultants review drawings, tenders and contracts, compare offers and point out savings that make a real difference to your final building cost.</p>
    </div>
    <svg class="abs" style="left:0;top:0" width="762" height="428" viewBox="0 0 762 428" font-family="Montserrat, sans-serif">
      <circle cx="111" cy="287" r="46" fill="none" stroke="#c9c9c9" stroke-width="5"/>
      <circle cx="111" cy="287" r="46" fill="none" stroke="#b47b0a" stroke-width="13" stroke-dasharray="144.5 289" transform="rotate(-90 111 287) scale(1 -1) translate(0 -574)"/>
      <text x="111" y="291" text-anchor="middle" font-size="10" font-weight="700" fill="#1d1d1d">50%</text>
      <circle cx="263" cy="287" r="46" fill="none" stroke="#c9c9c9" stroke-width="5"/>
      <circle cx="263" cy="287" r="46" fill="none" stroke="#b47b0a" stroke-width="13" stroke-dasharray="216.8 289" transform="rotate(-90 263 287)"/>
      <text x="263" y="291" text-anchor="middle" font-size="10" font-weight="700" fill="#1d1d1d">75%</text>
      <g font-family="Open Sans, sans-serif" font-size="7" font-weight="700" fill="#1d1d1d" text-anchor="middle">
        <text x="111" y="364">Add Your Text One</text><text x="263" y="364">Add Your Text Two</text>
      </g>
    </svg>
    <div class="item" style="left:436px;top:98px;width:260px"><span class="tick"></span><h4>Your Title Text Three</h4><p>Clear cost checks at every stage keep your project on budget and on time.</p></div>
    <div class="item" style="left:436px;top:150px;width:260px"><span class="tick"></span><h4>Your Title Text Three</h4><p>Clear cost checks at every stage keep your project on budget and on time.</p></div>
    <div class="item" style="left:436px;top:202px;width:260px"><span class="tick"></span><h4>Your Title Text Three</h4><p>Clear cost checks at every stage keep your project on budget and on time.</p></div>
    <div class="item" style="left:436px;top:254px;width:260px"><span class="tick"></span><h4>Your Title Text Three</h4><p>Clear cost checks at every stage keep your project on budget and on time.</p></div>
    <div class="item" style="left:436px;top:302px;width:260px"><span class="tick"></span><h4>Your Title Text Three</h4><p>Clear cost checks at every stage keep your project on budget and on time.</p></div>
  </section>

  <!-- About with features -->
  <section class="slide features" style="left:58px;top:991px">
    <div class="photo" role="img" aria-label="Photo of a smiling consultant in a blue suit and hard hat holding building plans" style="left:0;top:0;width:300px;height:428px;background:linear-gradient(170deg,#a9b3bb,#6f7f8f 40%,#2f4f8f 75%,#3a3a4a)"></div>
    <div class="band slant-right" style="left:510px;top:402px;width:252px;height:26px"></div>
    <div class="brand" style="left:592px;top:16px">
      <span class="brand-mark" style="width:11px;height:11px"></span>
      <span class="brand-name" style="font-size:13px">NIVEL CREST</span>
    </div>
    <div class="heading" style="left:324px;top:90px">About our <span class="accent">Nivel Crest</span></div>
    <div class="copy" style="left:324px;top:134px;width:370px">
      <p>We help builders plan every phase with care, so budgets hold, schedules stay firm and costly surprises on site are caught long before the first stone is laid.</p>
      <p>Our consultants review drawings, tenders and contracts, compare offers and point out savings that make a real difference to your final building cost.</p>
    </div>
    <div class="item" style="left:324px;top:222px"><span class="tick"></span><h4>Your Title Text Two</h4><p>Clear cost checks at every stage keep your project on budget and on time.</p></div>
    <div class="item" style="left:532px;top:222px"><span class="tick"></span><h4>Your Title Text Three</h4><p>Clear cost checks at every stage keep your project on budget and on time.</p></div>
    <div class="item" style="left:324px;top:294px"><span class="tick"></span><h4>Your Title Text Five</h4><p>Clear cost checks at every stage keep your project on budget and on time.</p></div>
    <div class="item" style="left:532px;top:294px"><span class="tick"></span><h4>Your Title Text Six</h4><p>Clear cost checks at every stage keep your project on budget and on time.</p></div>
  </section>

  <!-- Team member -->
  <section class="slide team" style="left:850px;top:990px">
    <div class="band" style="left:623px;top:0;width:139px;height:428px"></div>
    <div class="band slant-left" style="left:0;top:403px;width:250px;height:25px"></div>
    <div class="photo" role="img" aria-label="Portrait photo of a smiling bearded team member" style="left:425px;top:31px;width:305px;height:365px;background:linear-gradient(160deg,#c8cc3a 0%,#b7bb47 35%,#dcdcdc 60%,#f2f2f2 100%)"></div>
    <div class="brand" style="left:56px;top:40px;gap:9px">
      <span class="brand-mark" style="width:20px;height:20px"></span>
      <span class="brand-name" style="font-size:22px;letter-spacing:2px">NIVEL CREST</span>
    </div>
    <div class="heading" style="left:56px;top:106px">Lorem ipsum <span class="accent">dolor sit</span><br><span class="accent">amet</span></div>
    <div class="copy" style="left:56px;top:168px;width:290px">
      <p>We help builders plan every phase with care, so budgets hold, schedules stay firm and costly surprises on site are caught long before the first stone is laid.</p>
    </div>
    <svg class="abs" style="left:0;top:0" width="762" height="428" viewBox="0 0 762 428" fill="none" stroke="#b47b0a" stroke-width="2">
      <path d="M75 214 L100 239 L75 264 L50 239 Z"/>
      <path d="M75 273 L100 298 L75 323 L50 298 Z"/>
      <path d="M75 332 L100 357 L75 382 L50 357 Z"/>
      <g fill="#3a3a3a" stroke="none">
        <circle cx="69" cy="234" r="3.5"/><circle cx="81" cy="234" r="3.5"/><circle cx="75" cy="231" r="4"/>
        <rect x="63" y="239" width="24" height="7" rx="3.5"/>
        <path d="M62 296 L75 290 L88 296 L75 302 Z"/><path d="M67 299 L67 305 Q75 309 83 305 L83 299 L75 303 Z"/>
        <rect x="62" y="353" width="14" height="7" rx="3" transform="rotate(-20 69 356)"/>
        <rect x="74" y="353" width="14" height="7" rx="3" transform="rotate(20 81 356)"/>
      </g>
    </svg>
    <div class="item" style="left:73px;top:224px;width:280px"><h4>Your Title Text One</h4><p>Short summary of this service step, what it covers and how it saves money for builders.</p></div>
    <div class="item" style="left:73px;top:283px;width:280px"><h4>Your Title Text Two</h4><p>Short summary of this service step, what it covers and how it saves money for builders.</p></div>
    <div class="item" style="left:73px;top:342px;width:280px"><h4>Your Title Text Three</h4><p>Short summary of this service step, what it covers and how it saves money for builders.</p></div>
  </section>

  <!-- Closing -->
  <section class="slide closing" style="left:1648px;top:993px;background:var(--dark)">
    <div class="photo" role="img" aria-label="Photo of two business people shaking hands" style="left:0;top:0;width:762px;height:268px;background:linear-gradient(120deg,#5d6a7a,#3b4452 45%,#26303c 70%,#a7aeb6 100%)"></div>
    <div class="brand" style="left:30px;top:326px;gap:10px">
      <span class="brand-mark" style="width:26px;height:26px"></span>
      <span class="brand-name" style="font-size:30px;letter-spacing:3px">NIVEL CREST</span>
    </div>
    <div class="abs" style="left:440px;top:308px;font:800 46px Montserrat,sans-serif;color:#fff;letter-spacing:1px">THANK YOU</div>
    <div class="abs social" style="left:538px;top:381px;display:flex;gap:6px">
      <span style="width:14px;height:14px;border-radius:50%;background:var(--gold-light)"></span>
      <span style="width:14px;height:14px;border-radius:50%;background:var(--gold-light)"></span>
      <span style="width:14px;height:14px;border-radius:50%;background:var(--gold-light)"></span>
      <span style="width:14px;height:14px;border-radius:50%;background:var(--gold-light)"></span>
    </div>
  </section>

</div>
</body>
</html>
```